www.marvenholt.com

Updating website so looks futristic but yet business like and easy to navigate, essentially a good landing page with a cool picture summing up what we do, and links to the following pages, all other pages on site to be updated, Exclusive Distributor of Brisk Forge Unique Fitness Equipment Products in UK & Ireland, www.crestvolley.co.uk Exclusive Partners & Distributors Of Crest Volley - Obstacle Races - Obstacle Hire - Obstacle Training - Adventure Events, www.goplumwick.co.uk Adventures That Inspire. We also Health Club / Facillity Consultancy

```html
<!DOCTYPE html>
<html lang="en">
<head>
<meta charset="utf-8">
<title>Marvenholt Leisure — Health, Wellness, Fitness</title>
<link rel="stylesheet" href="https://fonts.googleapis.com/css2?family=Marcellus+SC&family=Lato:wght@400;700&family=Arimo:ital,wght@0,400;1,400&display=swap">
<style>
:root{
  --green:#4a8f14;
  --green-dark:#2f6a0c;
  --green-deep:#1f4a08;
  --grass:#3c7815;
  --lime:#d9f5a8;
  --lime-text:#7fc13a;
  --ink:#222;
  --grey:#666;
  --white:#fff;
}
*{box-sizing:border-box;margin:0;padding:0}
html,body{width:1200px;height:2731px;overflow:hidden}
body{font-family:"Arimo",Arial,sans-serif;color:var(--ink);background:var(--white);position:relative}
.heading{font-family:"Marcellus SC",serif;font-weight:400}
.topbar{height:40px;background:var(--green);display:flex;align-items:center;justify-content:space-between;padding:0 78px}
.topbar .social{display:flex;gap:8px}
.topbar .social span{width:28px;height:28px;border-radius:50%;background:var(--lime)}
.topbar .phone{color:var(--white);font-size:17px;display:flex;align-items:center;gap:8px}
.nav{height:66px;background:var(--white);position:relative;display:flex;align-items:center;justify-content:space-between;padding:0 78px;font-family:"Lato",sans-serif;font-size:17px;color:#444}
.nav ul{display:flex;list-style:none;gap:32px}
.nav li.active{color:var(--green-dark);font-weight:700;position:relative}
.nav li.active::after{content:"";position:absolute;left:50%;top:32px;margin-left:-9px;border:9px solid transparent;border-bottom-color:var(--green-dark)}
.brand{position:absolute;left:466px;top:-22px;width:268px;height:102px;background:var(--green-dark);border-radius:6px;color:var(--white);text-align:center;padding-top:18px;z-index:2}
.brand .name{font-family:"Marcellus SC",serif;font-size:27px}
.brand .tag{font-family:"Marcellus SC",serif;font-size:14px;margin-top:6px}
.hero{height:574px;position:relative;background:radial-gradient(ellipse at 55% 55%,#5d5f62 0%,#3b3d40 45%,#1d1f22 100%);text-align:center;color:var(--white)}
.hero .sub{padding-top:162px;font-family:"Marcellus SC",serif;font-size:25px}
.hero h1{font-family:"Lato",sans-serif;font-weight:400;font-size:62px;margin-top:4px}
.hero .actions{display:flex;justify-content:center;gap:22px;margin-top:26px}
.btn{display:inline-flex;align-items:center;justify-content:center;font-family:"Lato",sans-serif;font-size:21px;text-transform:uppercase}
.btn-solid{width:228px;height:56px;background:var(--green);color:var(--white)}
.btn-line{width:228px;height:56px;border:1px solid var(--green);color:var(--white)}
.hero .arrow{position:absolute;top:358px;width:46px;height:46px}
.hero .prev{left:18px}.hero .next{right:18px}
.services{height:500px;background:linear-gradient(#3f7d17,#2e6410);position:relative}
.cards{position:absolute;top:-34px;left:78px;display:flex;gap:23px}
.card{width:333px;height:447px;background:var(--green);padding:9px;text-align:center;color:var(--white)}
.card .photo{height:188px;background:linear-gradient(135deg,#c9d6c9,#7e9a85 50%,#b86c4a)}
.card h3{font-family:"Marcellus SC",serif;font-style:italic;font-size:30px;margin-top:14px;font-weight:400}
.card p{font-size:14px;line-height:25px;margin:8px 12px 0}
.btn-lime{width:188px;height:52px;background:var(--lime);color:#333;font-size:20px;margin-top:26px}
.team{height:559px;text-align:center}
.section-title{font-size:36px;color:var(--green-deep);padding-top:48px}
.members{display:flex;justify-content:space-between;padding:36px 100px 0}
.member{width:290px}
.member .avatar{width:122px;height:122px;border-radius:50%;margin:0 auto;background:radial-gradient(circle at 50% 40%,#8a8f86,#3c4036)}
.member h4{font-family:"Marcellus SC",serif;font-weight:400;font-size:22px;margin-top:26px;color:var(--green-deep)}
.member .role{font-size:14px;color:var(--green);line-height:20px;margin-top:8px;height:44px}
.member p{font-size:14px;color:var(--grey);line-height:25px;margin-top:8px}
.member .links{display:flex;justify-content:center;gap:11px;margin-top:24px}
.member .links span{width:36px;height:36px;border-radius:50%;background:var(--green)}
.member .links span:nth-child(even){background:var(--green-deep)}
.promo{height:313px;background:linear-gradient(90deg,#2f5e1d,#436f35 50%,#2f5e1d);text-align:center;color:var(--white)}
.promo h2{font-size:38px;padding-top:62px}
.promo p{font-size:14px;line-height:25px;width:740px;margin:10px auto 0}
.promo .btn-lime{width:166px;height:51px;margin-top:30px}
.blog{height:348px;text-align:center}
.posts{display:flex;gap:0;padding:40px 58px 0}
.post{width:361px;text-align:left;padding:10px 20px 30px;margin-right:2px;box-shadow:8px 0 12px -8px rgba(0,0,0,.18),-8px 0 12px -8px rgba(0,0,0,.18)}
.post:first-child{box-shadow:8px 0 12px -8px rgba(0,0,0,.18)}
.post:last-child{box-shadow:-8px 0 12px -8px rgba(0,0,0,.18)}
.post h5{font-family:"Lato",sans-serif;font-weight:400;font-size:21px;color:var(--lime-text)}
.post .date{font-style:italic;color:#999;font-size:14px;margin-top:12px;display:flex;align-items:center;gap:8px}
.post p{color:var(--grey);font-size:14px;line-height:25px;margin-top:12px}
.footer{height:270px;background:linear-gradient(90deg,#22491a,#39602e 50%,#22491a);padding:33px 78px 0;color:var(--white)}
.foot-nav{display:flex;align-items:center;justify-content:space-between;font-size:15px}
.foot-nav ul{display:flex;list-style:none;align-items:center}
.foot-nav li{padding:0 10px;border-left:1px solid var(--white);line-height:14px}
.foot-nav li.home{background:var(--green);width:80px;height:40px;line-height:40px;text-align:center;border:0;margin-right:14px;padding:0}
.foot-nav li:nth-child(2){border-left:1px solid var(--white)}
.foot-nav .social{display:flex;gap:10px}
.foot-nav .social span{width:42px;height:40px;background:var(--green)}
.footer hr{border:0;border-top:1px solid rgba(255,255,255,.6);margin-top:22px}
.footer h6{font-family:"Lato",sans-serif;font-weight:400;font-size:21px;margin-top:22px}
.contacts{display:flex;margin-top:10px;font-size:14px;line-height:23px}
.contact{display:flex;gap:18px;align-items:flex-start}
.contact .icon{width:53px;height:53px;background:var(--green);display:flex;align-items:center;justify-content:center;flex:none}
.contact span{padding-top:8px}
.contact:nth-child(1){width:266px}.contact:nth-child(2){width:262px}.contact:nth-child(3){width:268px}
.copyright{height:61px;background:var(--green);color:var(--white);font-size:14px;display:flex;align-items:center;justify-content:center;gap:4px}
.copyright b{font-weight:400;font-size:17px}
</style>
</head>
<body>
<header>
  <div class="topbar">
    <div class="social"><span></span><span></span><span></span><span></span><span></span></div>
    <div class="phone">
      <svg width="12" height="18" viewBox="0 0 12 18"><rect x="1" y="1" width="10" height="16" rx="2" fill="none" stroke="#fff" stroke-width="2"/><circle cx="6" cy="14" r="1" fill="#fff"/></svg>
      07500-419263
    </div>
  </div>
  <nav class="nav">
    <ul><li class="active">Home</li><li>Contact</li><li>Our Team</li><li>Testimonials</li></ul>
    <div class="brand"><div class="name">Marvenholt Leisure</div><div class="tag">Health, Wellness, Fitness, Consultants</div></div>
    <ul><li>Health</li><li>Wellness</li><li>Fitness</li><li>Brisk Forge</li></ul>
  </nav>
</header>

<section class="hero" role="img" aria-label="Gym photo of a man lifting a dumbbell on a bench in front of a weight rack">
  <div class="sub">Health, Wellness, Fitness</div>
  <h1>Marvenholt Leisure</h1>
  <div class="actions"><span class="btn btn-solid">Contact Us</span><span class="btn btn-line">Learn More</span></div>
  <svg class="arrow prev" viewBox="0 0 46 46"><circle cx="23" cy="23" r="22" fill="#9fd17a" stroke="#fff" stroke-width="1.5"/><path d="M27 12 L18 23 L27 34" fill="none" stroke="#fff" stroke-width="2"/></svg>
  <svg class="arrow next" viewBox="0 0 46 46"><circle cx="23" cy="23" r="22" fill="none" stroke="#fff" stroke-width="1.5"/><path d="M19 12 L28 23 L19 34" fill="none" stroke="#fff" stroke-width="2"/></svg>
</section>

<section class="services">
  <div class="cards">
    <article class="card">
      <div class="photo" role="img" aria-label="Women doing an aerobics class"></div>
      <h3>Health</h3>
      <p>Lorem Ipsum is simply dummy text of the printing and typesetting industry. Lorem Ipsum has been the industry's standard dummy text.</p>
      <span class="btn btn-lime">Read More</span>
    </article>
    <article class="card">
      <div class="photo" role="img" aria-label="Group exercising on gym machines" style="background:linear-gradient(135deg,#9fb9c9,#6d8a78 50%,#a65670)"></div>
      <h3>Wellness</h3>
      <p>Lorem Ipsum is simply dummy text of the printing and typesetting industry. Lorem Ipsum has been the industry's standard dummy text.</p>
      <span class="btn btn-lime">Read More</span>
    </article>
    <article class="card">
      <div class="photo" role="img" aria-label="Group of people walking together outdoors" style="background:linear-gradient(135deg,#e8ecef,#5a6f86 50%,#2d3a52)"></div>
      <h3>Fitness</h3>
      <p>Lorem Ipsum is simply dummy text of the printing and typesetting industry. Lorem Ipsum has been the industry's standard dummy text.</p>
      <span class="btn btn-lime">Read More</span>
    </article>
  </div>
</section>

<section class="team">
  <h2 class="heading section-title">Meet Our team</h2>
  <div class="members">
    <div class="member">
      <div class="avatar" role="img" aria-label="Portrait of Dorian Vale"></div>
      <h4>Dorian Vale</h4>
      <div class="role">A leading life coach,self<br>development guru</div>
      <p>Lorem Ipsum is simply dummy text of the printing and typesetting industry. Lorem Ipsum has been the industry's.</p>
      <div class="links"><span></span><span></span><span></span><span></span></div>
    </div>
    <div class="member">
      <div class="avatar" role="img" aria-label="Portrait of Simon Carrow" style="background:radial-gradient(circle at 50% 40%,#7fa06a,#2a3a24)"></div>
      <h4>Simon Carrow</h4>
      <div class="role">Founder and owner of<br>Trailquick</div>
      <p>Lorem Ipsum is simply dummy text of the printing and typesetting industry. Lorem Ipsum has been the industry's.</p>
      <div class="links"><span></span><span></span><span></span><span></span></div>
    </div>
    <div class="member">
      <div class="avatar" role="img" aria-label="Portrait of Rob Ellery training outdoors" style="background:radial-gradient(circle at 50% 40%,#b08a58,#3d3a22)"></div>
      <h4>Rob Ellery</h4>
      <div class="role">A&nbsp;&nbsp;&nbsp;Powerhouse of fitness<br>knowledge</div>
      <p>Lorem Ipsum is simply dummy text of the printing and typesetting industry. Lorem Ipsum has been the industry's.</p>
      <div class="links"><span></span><span></span><span></span><span></span></div>
    </div>
  </div>
</section>

<section class="promo" role="img" aria-label="Green tinted photo of people on exercise bikes">
  <h2 class="heading">Brisk Forge</h2>
  <p>Lorem Ipsum is simply dummy text of the printing and typesetting industry. Lorem Ipsum has been the industry's standard dummy text ever since the 1500s, when an unknown printer took a galley Lorem Ipsum has been the industry's standard dummy text ever since the 1500s, when an unknown printer took a galley.</p>
  <span class="btn btn-lime">Join Now</span>
</section>

<section class="blog">
  <h2 class="heading section-title">Latest Blog</h2>
  <div class="posts">
    <article class="post">
      <h5>Lorem Ipsum is simply dummy</h5>
      <div class="date"><svg width="14" height="14" viewBox="0 0 14 14"><rect x="1" y="2" width="12" height="11" fill="#bbb"/><rect x="1" y="2" width="12" height="3" fill="#999"/></svg>Posted at 10-10-2017</div>
      <p>Lorem Ipsum is simply dummy text of the printing and typesetting industry. Lorem Ipsum has been the industry's standard</p>
    </article>
    <article class="post">
      <h5>Lorem Ipsum is simply dummy</h5>
      <div class="date"><svg width="14" height="14" viewBox="0 0 14 14"><rect x="1" y="2" width="12" height="11" fill="#bbb"/><rect x="1" y="2" width="12" height="3" fill="#999"/></svg>Posted at 10-10-2017</div>
      <p>Lorem Ipsum is simply dummy text of the printing and typesetting industry. Lorem Ipsum has been the industry's standard</p>
    </article>
    <article class="post">
      <h5>Lorem Ipsum is simply dummy</h5>
      <div class="date"><svg width="14" height="14" viewBox="0 0 14 14"><rect x="1" y="2" width="12" height="11" fill="#bbb"/><rect x="1" y="2" width="12" height="3" fill="#999"/></svg>Posted at 10-10-2017</div>
      <p>Lorem Ipsum is simply dummy text of the printing and typesetting industry. Lorem Ipsum has been the industry's standard</p>
    </article>
  </div>
</section>

<footer class="footer" role="img" aria-label="Dark green tinted gym photo behind the footer">
  <div class="foot-nav">
    <ul><li class="home">Home</li><li>Contact</li><li>Our Team</li><li>Testimonial</li><li>Health</li><li>Wellness</li><li>Fitness</li><li>Brisk Forge</li></ul>
    <div class="social"><span></span><span></span><span></span></div>
  </div>
  <hr>
  <h6>CONTACT US</h6>
  <div class="contacts">
    <div class="contact">
      <div class="icon"><svg width="20" height="26" viewBox="0 0 20 26"><path d="M10 1a8 8 0 0 0-8 8c0 6 8 15 8 15s8-9 8-15a8 8 0 0 0-8-8z" fill="none" stroke="#fff" stroke-width="2"/><circle cx="10" cy="9" r="3" fill="#fff"/></svg></div>
      <span>Marvenholt Leisure<br>The Orchards Cheshire<br>UK &amp; Ireland</span>
    </div>
    <div class="contact">
      <div class="icon"><svg width="22" height="22" viewBox="0 0 22 22"><path d="M5 2l4 4-2 3c1 3 3 5 6 6l3-2 4 4-3 3C9 20 2 13 2 5z" fill="none" stroke="#fff" stroke-width="1.8" stroke-linejoin="round"/></svg></div>
      <span>07500-419263</span>
    </div>
    <div class="contact">
      <div class="icon"><svg width="24" height="22" viewBox="0 0 24 22"><rect x="6" y="1" width="12" height="6" fill="none" stroke="#fff" stroke-width="2"/><rect x="2" y="7" width="20" height="9" fill="#fff"/><rect x="6" y="13" width="12" height="8" fill="#4a8f14" stroke="#fff" stroke-width="2"/></svg></div>
      <span>07500-419263</span>
    </div>
    <div class="contact">
      <div class="icon"><svg width="24" height="18" viewBox="0 0 24 18"><rect x="1" y="1" width="22" height="16" fill="none" stroke="#fff" stroke-width="2"/><path d="M1 1l11 9 11-9" fill="none" stroke="#fff" stroke-width="2"/></svg></div>
      <span>info@marvenholt.com</span>
    </div>
  </div>
</footer>
<div class="copyright">Copyright | 2017 <b>MARVENHOLT LEISURE</b>. All Rights Reserved.</div>
</body>
</html>
```